Pictorama Business Card For Comedian

Hi,

I'd like a 2-sided business card that kind mimics an Pictorama page. I've attached screenshots with the copy and language that should be written on there.

I'd like it to be way more stylized and a bit more creative than what I did on Powerpoint. I just did a mockup so that you can have an idea. I'd like it to be designed and you to take a bit of creative imagery so that it doesn't look so static and monochromatic.

PLEASE BE CREATIVE WITH THESE DESIGNS. I DON'T WANT IT TO LOOK EXACTLY LIKE THE ATTACHED IMAGE OR EXACTLY LIKE AN PICTORAMA PAGE. I want to use it as inspiration to create something that looks more sleek, and creative. I don't want the colors to just be boring gray, and blue. Have fun and spice it up a bit!

Check out my website MauraVelinski.com to see the colors and fonts I use for my branding.

For the main photo: Here's a link with the hi-res photo: !https://www.filecrate.net/s/q8x4tmbw2rzplkd/Maura-Velinski-C73K2251.jpg?dl=0

For the thumbnail icon photo, you can use this: https://www.filecrate.net/s/vh5ntrx9gqwmyle/Maura%20Velinski%20Tide%20Glass%20Headshot.jpg?dl=0

Use the Standard Business Card Template from Prinzo.com:
https://help.prinzo.com/hc/en-us/article_attachments/318842907/Standard_Size__US__Business_Cards_Portrait.jpg

Please let me know if you have any questions.

Industry/Entity Type

Business

Contact Information for Business Card

All of the text and copy has been provided on the attached jpg.

Colors
33a6d7
0255a3
aaaaaa
dbdbdb
1b1b1b

Requirements
Should not have
• A Hyperlink for the Email Addresses

```html
<!DOCTYPE html>
<html lang="en">
<head>
<meta charset="utf-8">
<title>Maura Velinski — Business Card</title>
<link href="https://fonts.googleapis.com/css2?family=Source+Sans+3:ital,wght@0,400;0,600;0,700;1,700&family=Yellowtail&display=swap" rel="stylesheet">
<style>
  :root {
    --stage: #545454;
    --card: #ffffff;
    --brand-blue: #318bc4;
    --name-blue: #2e88c6;
    --coral: #f7968a;
    --ink: #3a3a3a;
    --photo-dark: #1e1715;
    --photo-warm: #c9705f;
  }
  html, body {
    margin: 0;
    width: 1200px;
    height: 900px;
    overflow: hidden;
    background: var(--stage);
    font-family: "Source Sans 3", Arial, sans-serif;
    color: var(--ink);
  }
  .stage { position: relative; width: 1200px; height: 900px; }
  .card {
    position: absolute;
    top: 170px;
    width: 347px;
    height: 561px;
    background: var(--card);
    box-shadow: 3px 3px 5px rgba(0,0,0,0.45);
    text-align: center;
  }
  .card--front { left: 259px; }
  .card--back { left: 631px; }
  .abs { position: absolute; left: 0; right: 0; margin: 0; }

  .portrait {
    position: absolute;
    left: 58px; top: 38px;
    width: 230px; height: 283px;
    border-radius: 50%;
    background: radial-gradient(ellipse at 50% 40%, #7a4a3a 0%, var(--photo-dark) 45%, var(--photo-dark) 62%, var(--photo-warm) 82%, #f08a74 100%);
  }
  .script-name {
    top: 346px;
    font-family: "Yellowtail", cursive;
    font-size: 36px;
    color: var(--name-blue);
    line-height: 1;
  }
  .roles { font-size: 15px; letter-spacing: 0.2px; line-height: 1; }
  .front-roles { top: 392px; }
  .band {
    position: absolute; left: 0; right: 0;
    color: #fff; font-weight: 600; font-size: 18px;
    display: flex; align-items: center; justify-content: center;
  }
  .band--bookings { top: 444px; height: 33px; background: var(--coral); }
  .booking-list { top: 484px; font-size: 16px; line-height: 22px; }

  .back-name { top: 53px; font-size: 22px; font-weight: 600; color: var(--name-blue); line-height: 1; }
  .back-roles { top: 79px; font-size: 16px; }
  .website { top: 108px; font-size: 18px; line-height: 1; }
  .band--info { top: 154px; height: 33px; background: var(--brand-blue); }
  .social-dots { top: 201px; display: flex; justify-content: center; gap: 4px; }
  .social-dot { width: 20px; height: 20px; border: 1.5px solid #222; border-radius: 50%; box-sizing: border-box; }
  .social-list { top: 229px; font-size: 17px; line-height: 23px; }
  .band--about { top: 315px; height: 39px; background: var(--brand-blue); }
  .about-text { top: 369px; left: 30px; right: 30px; font-size: 16px; line-height: 21px; }
  .band--connect { top: 502px; height: 39px; background: var(--brand-blue); font-style: italic; font-weight: 700; }
</style>
</head>
<body>
<main class="stage">
  <section class="card card--front">
    <div class="portrait" role="img" aria-label="Headshot portrait of the comedian"></div>
    <p class="abs script-name">Maura Velinski</p>
    <p class="abs roles front-roles">COMEDIAN | ACTOR | WRITER</p>
    <div class="band band--bookings">FOR BOOKINGS</div>
    <p class="abs booking-list">Jolene@BrightMarbleTalent.com<br>Dana.Pellworth@orvx.com</p>
  </section>

  <section class="card card--back">
    <p class="abs back-name">MAURA VELINSKI</p>
    <p class="abs roles back-roles">COMEDIAN | ACTOR | WRITER</p>
    <p class="abs website">www.mauravelinski.com</p>
    <div class="band band--info">MORE INFO</div>
    <div class="abs social-dots">
      <span class="social-dot"></span><span class="social-dot"></span><span class="social-dot"></span>
    </div>
    <p class="abs social-list">Friendbook.com/mauravelinski<br>Chirper.com/wittymaura<br>Pictorama.com/wittymaura</p>
    <div class="band band--about">ABOUT ME</div>
    <p class="abs about-text">Stand Up Comedian. I Host. I write. I Dance. I Do Not Sing Unless I'm in the Shower. I Accept Tips. (Not on jokes, but on Paylo.<br>As seen on Halo TV, Laugh Channel, Beat TV, Real TV, Verve, and Pulse.</p>
    <div class="band band--connect">Lets Stay Connected !</div>
  </section>
</main>
</body>
</html>
```